E-learning Information & Community Website Needs a Makeover

I'm looking for a design makeover for my website "Tavipor.club". Tavipor's aim is to connect people to online learning through forums, information, guides & independent reviews. The site was launched in September 2014 using a forum software (Xenforo), but now needs a more polished and sophisticated look which communicates expertise and professionalism. I would like to see designs that use the current "Tavipor" blue (#0070c0). To visit the current website, go to http://www.tavipor.club/

Target Market(s)

People wishing to study online

Industry/Entity Type

Club

Number of Pages Required

4 page

Font styles to use
Sans Serif

Requirements
Must have
• A simple, clear and sophisticated lading page with links to the site's key features: discussion forums, Useful resources, Reviews, News etc, Articles. (See layout idea file attached)
• The main pages are the Landing Page, Discussion Forums, Resources & Reviews
• I would like to see designs that use the current "Tavipor" blue (#0070c0).
Nice to have
• Something uncluttered and easy to understand. The design should convey expertise in the field of online learning, giving users a sense of trust in the site's offerings.
• To give an idea of the sort of thing I'm after, take a look at wendricast.com website (screenshot attached)

```html
<!DOCTYPE html>
<html lang="en">
<head>
<meta charset="utf-8">
<title>Tavipor – Connecting People to Online Learning</title>
<link rel="stylesheet" href="https://fonts.googleapis.com/css2?family=Open+Sans:ital,wght@0,300;0,400;0,600;1,400&display=swap">
<style>
:root{
  --brand:#0070c0;
  --link:#1a9ee0;
  --ink:#222;
  --muted:#777;
  --panel:#efefef;
  --btn:#7a7a7a;
  --rule:#cfcfcf;
  --white:#fff;
  --red:#e8192c;
  --orange:#f7a600;
  --tag:#b5b5b5;
  --tag-dark:#8c8c8c;
}
*{box-sizing:border-box;margin:0;padding:0}
html,body{width:960px;height:1200px;overflow:hidden;background:var(--white)}
body{position:relative;font-family:"Open Sans",Arial,sans-serif;color:var(--ink)}
.abs{position:absolute}

/* header */
.site-header{left:0;top:0;width:960px;height:53px;background:var(--brand)}
.brand{left:179px;top:3px;color:#9fd0f5;font-size:23px;font-weight:400;letter-spacing:.2px}
.tagline{left:178px;top:33px;color:var(--white);font-size:11px;font-weight:600}
.main-nav{left:411px;top:16px;display:flex;gap:12px;font-size:9.5px;color:var(--white)}
.nav-pointer{left:418px;top:0}
.social{display:flex;gap:3px}
.social span{width:14px;height:14px;border-radius:50%;display:block}
.header-social{left:543px;top:32px}
.newsletter-input{left:614px;top:33px;width:133px;height:15px;background:var(--white);font-size:6.5px;font-style:italic;color:#888;padding:2px 4px}
.subscribe{left:750px;top:34px;font-size:8.5px;font-style:italic;color:#111}

/* hero */
.hero-photo{left:160px;top:53px;width:636px;height:268px;background:radial-gradient(ellipse at 70% 40%,#c9ced6 0%,#e4e7eb 45%,#f7f8f9 80%,#fff 100%)}
.hero-copy{left:200px;top:92px}
.hero-copy .lead{font-size:14px;font-weight:300;color:#333}
.hero-copy .lead b{font-weight:400}
.hero-copy .big{font-size:29px;font-weight:300;line-height:1.2;color:#222}
.hero-copy .big b{font-weight:400}
.hero-copy .cta{font-size:14px;color:#555}
.hero-copy .cta em{color:#222}
.hero-copy .cta span{color:var(--brand)}
.dots{left:442px;top:293px;display:flex;gap:3px}
.dots i{width:9px;height:9px;border-radius:50%;background:#c7c7c7;display:block}
.dots i.on{background:var(--brand)}

/* features */
.features{left:2px;top:321px;width:958px;height:374px;background:var(--panel)}
.feature{width:197px}
.feature h3{font-size:14.5px;font-weight:400;color:#222;padding:0 0 5px 15px;border-bottom:2px solid #d8d8d8;position:relative;white-space:nowrap}
.feature h3::before{content:"";position:absolute;left:0;top:6px;border-left:7px solid #111;border-top:4px solid transparent;border-bottom:4px solid transparent}
.feature p{font-size:7.9px;line-height:11px;color:#666;text-align:justify;hyphens:none;margin-top:13px;height:90px}
.feature p .nb{white-space:nowrap}
.actions{display:flex;justify-content:space-between;white-space:nowrap}
.btn{display:inline-block;background:var(--btn);color:var(--white);font-size:11px;padding:4px 14px;border:1px solid #666}
.btn-signup{background:var(--brand);font-style:italic;font-size:10.5px;padding:4px 5px;border-color:#0a5a95}

/* topics */
.section-title{left:0;width:960px;text-align:center;font-size:25px;font-weight:300;color:#222;letter-spacing:.5px}
.topic-strip{left:163px;top:743px;width:650px;height:57px;background:#f4f4f4;display:flex;align-items:center;justify-content:space-around;padding:0 10px}
.topic{font-size:13px;color:#222;display:flex;align-items:center;gap:5px}
.topic i{width:30px;height:30px;border-radius:50%;background:#222;display:block}

/* threads */
.thread-head-band{left:2px;top:866px;width:958px;height:32px;background:var(--panel)}
.thread-head{top:877px;font-size:8.5px;color:#222}
.thread-list{left:173px;top:905px;width:603px;background:var(--white);border:1px solid #eee}
.thread{height:43.6px;display:flex;align-items:center;border-bottom:1px solid #e6e6e6;position:relative}
.thread:last-child{border-bottom:none}
.avatar{width:30px;height:30px;margin-left:6px;border-radius:4px;flex:none}
.avatar-photo{background:linear-gradient(135deg,#b59a82,#6e5645);border:1px solid #aaa}
.avatar-brand{background:var(--brand);color:var(--white);font-size:6.5px;display:flex;align-items:center;justify-content:center}
.thread-main{margin-left:6px;width:322px}
.thread-title{font-size:12px;letter-spacing:-.15px;color:var(--link);line-height:15px}
.tag{font-size:8.5px;letter-spacing:0;padding:0 4px;border-radius:2px;margin-right:3px;vertical-align:1px}
.tag-article{background:var(--red);color:var(--white)}
.tag-courses{background:var(--orange);color:#222}
.tag-news{background:var(--tag);color:#222}
.tag-event{background:var(--tag-dark);color:#222}
.thread-meta{font-size:8.5px;color:#888;white-space:nowrap}
.thread-stats{position:absolute;left:367px;top:5px;bottom:5px;border-left:1px solid #ddd;padding-left:7px;width:100px}
.stat-row{display:flex;justify-content:space-between;font-size:11.5px;color:#777}
.stat-row.small{font-size:8.5px}
.stat-row .num{color:#222}
.stat-row .num.hot{color:#c0143c}
.thread-last{position:absolute;right:4px;top:7px;text-align:right}
.thread-last .who{font-size:12.5px;color:var(--link);line-height:15px}
.thread-last .when{font-size:8.5px;color:#888}

/* footer */
.site-footer{left:2px;top:1143px;width:958px;height:57px;background:var(--brand)}
.footer-nav{left:180px;top:1171px;display:flex;gap:10px;font-size:8.5px;color:var(--white)}
.footer-social{left:720px;top:1166px}
</style>
</head>
<body>

<header class="site-header abs"></header>
<svg class="nav-pointer abs" width="10" height="6" viewBox="0 0 10 6"><path d="M0 0h10L5 6z" fill="#fff"/></svg>
<div class="brand abs">Tavipor</div>
<div class="tagline abs">Connecting People to Online Learning</div>
<nav class="main-nav abs">
  <span>Home</span><span>Forums</span><span>Resources</span><span>Members</span><span>FAQ</span><span>Blog</span><span>Tavipor Español</span><span>Course Scoop</span><span>Login</span>
</nav>
<div class="social header-social abs">
  <span style="background:#3b5a98"></span><span style="background:#1da1f2"></span><span style="background:#e02a20"></span><span style="background:#dd4b39"></span>
</div>
<div class="newsletter-input abs">Subscribe for Monthly Newsletter</div>
<div class="subscribe abs">Subscribe</div>

<div class="hero-photo abs" role="img" aria-label="Overhead photo of people sitting in chairs around a round white table with laptops"></div>
<div class="hero-copy abs">
  <div class="lead">At the heart of <b>connecting people</b></div>
  <div class="big">to <b>online</b> learning</div>
  <div class="cta"><span>Sign Up.</span> Its <em>Free</em></div>
</div>
<div class="dots abs"><i class="on"></i><i></i><i></i><i></i><i></i></div>

<section class="features abs"></section>

<article class="feature abs" style="left:176px;top:361px">
  <h3>Getting Started</h3>
  <p>Tavipor.club is a Forum and Community Website for Consumers and Providers of MOOCs and Online Learning to meet, share, debate and learn. The site aims to provide its users with a centralised space to interact with peers around a common theme: <span class="nb">E-learning.</span></p>
  <div class="actions"><span class="btn">Read more</span><span class="btn btn-signup">Sign up! Its Free</span></div>
</article>
<article class="feature abs" style="left:381px;top:363px">
  <h3>Discussions</h3>
  <p>Tavipor.club is a Forum and Community Website for Consumers and Providers of MOOCs and Online Learning to meet, share, debate and learn. The site aims to provide its users with a centralised space to interact with peers around a common theme: <span class="nb">E-learning.</span></p>
  <div class="actions"><span class="btn">Read more</span></div>
</article>
<article class="feature abs" style="left:585px;top:363px">
  <h3>Reviews</h3>
  <p>Tavipor.club is a Forum and Community Website for Consumers and Providers of MOOCs and Online Learning to meet, share, debate and learn. The site aims to provide its users with a centralised space to interact with peers around a common theme: <span class="nb">E-learning.</span></p>
  <div class="actions"><span class="btn">Read more</span></div>
</article>
<article class="feature abs" style="left:176px;top:531px">
  <h3>Tips &amp; Guidelines</h3>
  <p>Tavipor.club is a Forum and Community Website for Consumers and Providers of MOOCs and Online Learning to meet, share, debate and learn. The site aims to provide its users with a centralised space to interact with peers around a common theme: <span class="nb">E-learning.</span></p>
  <div class="actions"><span class="btn">Read more</span></div>
</article>
<article class="feature abs" style="left:381px;top:527px">
  <h3>News &amp; Articles</h3>
  <p>Tavipor.club is a Forum and Community Website for Consumers and Providers of MOOCs and Online Learning to meet, share, debate and learn. The site aims to provide its users with a centralised space to interact with peers around a common theme: <span class="nb">E-learning.</span></p>
  <div class="actions"><span class="btn">Read more</span></div>
</article>
<article class="feature abs" style="left:585px;top:527px">
  <h3>Newsletter</h3>
  <p>Tavipor.club is a Forum and Community Website for Consumers and Providers of MOOCs and Online Learning to meet, share, debate and learn. The site aims to provide its users with a centralised space to interact with peers around a common theme: <span class="nb">E-learning.</span></p>
  <div class="actions"><span class="btn">Read more</span></div>
</article>

<h2 class="section-title abs" style="top:705px">FREQUENT TOPICS</h2>
<div class="topic-strip abs">
  <span class="topic"><i></i></span>
  <span class="topic">Alder Vale</span>
  <span class="topic">Ridgecrest</span>
  <span class="topic">Kestrow</span>
  <span class="topic">Halbrook</span>
  <span class="topic">Pinefield Global</span>
  <span class="topic" style="width:24px;height:34px;border:1px solid #333;background:#fafafa"></span>
</div>

<h2 class="section-title abs" style="top:825px">FROM THE COMMUNITY</h2>
<div class="thread-head-band abs"></div>
<div class="thread-head abs" style="left:189px">RECENT THREADS</div>
<div class="thread-head abs" style="left:481px">START DATE</div>
<div class="thread-head abs" style="left:581px">REPLIES</div>
<div class="thread-head abs" style="left:632px">VIEWS</div>
<div class="thread-head abs" style="left:695px">LAST MESSAGE</div>

<div class="thread-list abs">
  <div class="thread">
    <div class="avatar avatar-photo" role="img" aria-label="Member profile photo"></div>
    <div class="thread-main">
      <div class="thread-title"><span class="tag tag-article">Article</span>Wellcom to Navelo, the new catalan MOOC directory</div>
      <div class="thread-meta">Oriol Vantessa, Yesterday at 7:02 PM, Blog</div>
    </div>
    <div class="thread-stats"><div class="stat-row"><span>Replies:</span><span class="num">0</span></div><div class="stat-row small"><span>Views:</span><span class="num">28</span></div></div>
    <div class="thread-last"><div class="who">Oriol Vantessa</div><div class="when">Yesterday at 7:02 PM</div></div>
  </div>
  <div class="thread">
    <div class="avatar avatar-brand">Tavipor</div>
    <div class="thread-main">
      <div class="thread-title"><span class="tag tag-courses">Courses</span>Quenrix MOOCs</div>
      <div class="thread-meta">Marisol, Yesterday at 9:30 AM, Lumora</div>
    </div>
    <div class="thread-stats"><div class="stat-row"><span>Replies:</span><span class="num">0</span></div><div class="stat-row small"><span>Views:</span><span class="num">55</span></div></div>
    <div class="thread-last"><div class="who">Marisol</div><div class="when">Yesterday at 9:30 AM</div></div>
  </div>
  <div class="thread">
    <div class="avatar avatar-brand">Tavipor</div>
    <div class="thread-main">
      <div class="thread-title"><span class="tag tag-news">News</span>Tavipor's Course Scoop promoted to Gold level!</div>
      <div class="thread-meta">Marisol, Monday at 6:24 PM, MOOC News</div>
    </div>
    <div class="thread-stats"><div class="stat-row"><span>Replies:</span><span class="num hot">1</span></div><div class="stat-row small"><span>Views:</span><span class="num">47</span></div></div>
    <div class="thread-last"><div class="who">Tomek</div><div class="when">Tuesday at 2:14 PM</div></div>
  </div>
  <div class="thread">
    <div class="avatar avatar-brand">Tavipor</div>
    <div class="thread-main">
      <div class="thread-title"><span class="tag tag-news">News</span>Brightmoor Academy are looking for a video star!</div>
      <div class="thread-meta">Marisol, Tuesday at 8:41 AM, General stuff on course providers</div>
    </div>
    <div class="thread-stats"><div class="stat-row"><span>Replies:</span><span class="num">0</span></div><div class="stat-row small"><span>Views:</span><span class="num">116</span></div></div>
    <div class="thread-last"><div class="who">Marisol</div><div class="when">Tuesday at 8:41 AM</div></div>
  </div>
  <div class="thread">
    <div class="avatar avatar-brand">Tavipor</div>
    <div class="thread-main">
      <div class="thread-title"><span class="tag tag-event">Event</span>What Reviews divulge about Online Education</div>
      <div class="thread-meta">Marisol, Monday at 10:52 AM, Events</div>
    </div>
    <div class="thread-stats"><div class="stat-row"><span>Replies:</span><span class="num">0</span></div><div class="stat-row small"><span>Views:</span><span class="num">76</span></div></div>
    <div class="thread-last"><div class="who">Marisol</div><div class="when">Monday at 10:52 AM</div></div>
  </div>
</div>

<footer class="site-footer abs"></footer>
<nav class="footer-nav abs">
  <span>Home</span><span>Forums</span><span>Resources</span><span>Members</span><span>FAQ</span><span>Blog</span><span>Tavipor Español</span><span>Course Scoop</span><span>Login</span>
</nav>
<div class="social footer-social abs">
  <span style="background:#3b5a98"></span><span style="background:#1da1f2"></span><span style="background:#e02a20"></span><span style="background:#dd4b39"></span>
</div>

</body>
</html>
```